Business Card for my New Brokerage

Looking to get a business card design for my new Real Estate Brokerage.
I want it with Picture, Phone Number, Email, Website, Office Address
Name and Designation. Please add logo too.

Target Market(s)

Real Estate Investors or Home Buyers

Industry/Entity Type

Real Estate

Contact Information for Business Card

Name, Email, Phone Number, website, email, office address

Colors
EB3D1F
EC4F4E
F09395
F8D3D4
FCEDEE

Requirements
Must have
• Minimalistic, Clean, Modern, Photo
Nice to have
• White and Red Colors

```html
<!DOCTYPE html>
<html lang="en">
<head>
<meta charset="utf-8">
<title>Ember Realty Inc – Business Card</title>
<link href="https://fonts.googleapis.com/css2?family=Lato:wght@400;700;900&family=Montserrat:wght@600&display=swap" rel="stylesheet">
<style>
  :root {
    --brand-red: #de0000;
    --paper: #ffffff;
    --paper-tint: #fcfaf3;
    --stage: #a3a3a3;
    --photo-light: #ecebe8;
    --photo-mid: #d9d8d4;
    --photo-dark: #3a3a3a;
    --text-light: #ffffff;
  }
  * { margin: 0; padding: 0; box-sizing: border-box; }
  html, body { width: 1200px; height: 1200px; overflow: hidden; }
  body {
    background: var(--stage);
    position: relative;
    font-family: "Lato", Arial, sans-serif;
  }
  .card {
    position: absolute;
    top: 303px;
    height: 594px;
    background: var(--paper);
    box-shadow: 3px 3px 4px rgba(0,0,0,0.45);
    overflow: hidden;
  }
  .card--front { left: 201px; width: 369px; }
  .card--back { left: 599px; width: 364px; }

  .front-texture {
    position: absolute; inset: 0;
    background: var(--paper-tint);
  }
  .brand {
    position: absolute;
    left: 0; right: 0;
    top: 228px;
    text-align: center;
    font-family: "Montserrat", Arial, sans-serif;
    font-weight: 600;
    color: var(--brand-red);
  }
  .brand__name {
    font-size: 56px;
    line-height: 1;
    letter-spacing: 1px;
  }
  .brand__name .brand__dot {
    display: inline-block;
    width: 10px; height: 10px;
    background: var(--brand-red);
    margin-left: 4px;
    vertical-align: baseline;
  }
  .brand__sub {
    font-size: 18px;
    letter-spacing: 5px;
    margin-top: 6px;
  }
  .front-url {
    position: absolute;
    left: 0; right: 0;
    top: 536px;
    text-align: center;
    font-size: 17px;
    letter-spacing: 0.8px;
    color: var(--brand-red);
  }

  .portrait {
    position: absolute;
    left: 0; right: 0;
    top: 8px; height: 323px;
    background: linear-gradient(180deg, var(--photo-light) 0%, var(--photo-mid) 65%, var(--photo-dark) 100%);
  }
  .contact-panel {
    position: absolute;
    left: 0; right: 0;
    top: 331px; bottom: 0;
    background: var(--brand-red);
    color: var(--text-light);
    text-align: center;
  }
  .contact-panel__name {
    position: absolute; left: 0; right: 0; top: 34px;
    font-weight: 900;
    font-size: 25px;
    letter-spacing: 0.3px;
  }
  .contact-panel__role {
    position: absolute; left: 0; right: 0; top: 62px;
    font-size: 17px;
  }
  .divider {
    position: absolute;
    left: 152px; width: 59px; height: 1px;
    background: var(--text-light);
  }
  .divider--top { top: 94px; }
  .divider--bottom { top: 184px; }
  .contact-list {
    position: absolute; left: 0; right: 0; top: 106px;
    list-style: none;
    font-size: 17px;
    line-height: 23px;
  }
  .address {
    position: absolute; left: 0; right: 0; top: 194px;
    font-style: normal;
    font-size: 17px;
    line-height: 22px;
  }
</style>
</head>
<body>
  <section class="card card--front">
    <div class="front-texture" role="img" aria-label="Subtle cream decorative pattern background"></div>
    <div class="brand">
      <div class="brand__name">EMBER<span class="brand__dot"></span></div>
      <div class="brand__sub">REALTY INC</div>
    </div>
    <div class="front-url">www.emberrealty.com</div>
  </section>

  <section class="card card--back">
    <div class="portrait" role="img" aria-label="Portrait photo of the managing director in a dark suit against a light wall"></div>
    <div class="contact-panel">
      <h1 class="contact-panel__name">MARCUS BELL</h1>
      <p class="contact-panel__role">Managing Director</p>
      <div class="divider divider--top"></div>
      <ul class="contact-list">
        <li>044-555 018 274</li>
        <li>hello@emberrealty.com</li>
        <li>www.emberrealty.com</li>
      </ul>
      <div class="divider divider--bottom"></div>
      <address class="address">215 Maple Row, Suite 4<br>Riverton Bay, 38617</address>
    </div>
  </section>
</body>
</html>
```